Business Card Design - Photographer

I am a landscape photographer and I require a business card design. 

I require two designs:
1)  a double sided business card
 and
b)  a single sided business card 

The single sided design can either be the same as the double sided (with just one side having all the information)....or it can be an entire new design. Its up to you.

My corporate colours are (CMYK):

Blue   69, 32, 0, 0
Grey  72,  64,  47,  31
Green  32,  2,  91,  0
Yellow   0, 19, 92, 0
Orange  0, 39, 75, 0

Colour space in final file should be in CMYK.

The details that need to be included on the card:

- Use the provided Logo
- Name: Wiktor Baranowski
- Email:   sales@vistalumeworks.com.au
- Website:    vistalumeworks.com.au
- Twitter:    twitter.com/vistalumeworks
- Facebook:   facebook.com/vistalumeworks
- Mobile  0417 539 662

Please use the attached template to design the logo to the specified size, including the marked bleed lines. I have also attached my logo in PNG (transparent background) and ai format for you to use.

The final file should be:
- Photoshop version with layers so I can edit the name/text etc. All non vector files should be high resolution at 1039 x 697 pixels at 300 dpi.

I also require a file as:
- Vector based PDF

Anyway questions please contact me.

Thank you

Industry/Entity Type

Landscape

Logo styles of interest
Pictorial/Combination Logo
Abstract Logo
Wordmark Logo
Lettermark Logo
Requirements
Must have
• The details that need to be included on the card:

- Use the provided Logo
- Name: Wiktor Baranowski
- Email: sales@vistalumeworks.com.au
- Website: vistalumeworks.com.au
- Twitter: twitter.com/vistalumeworks
- Facebook: facebook.com/vistalumeworks
- Mobile 0417 539 662

```html
<!DOCTYPE html>
<html lang="en">
<head>
<meta charset="utf-8">
<title>Vistalume Works – Business Cards</title>
<link rel="stylesheet" href="https://fonts.googleapis.com/css2?family=Marcellus&family=Tinos&family=Lato:wght@400&display=swap">
<style>
  :root {
    --backdrop: #ece8e3;
    --card: #ffffff;
    --card-edge: #4a3a2c;
    --ink: #3d4456;
    --grey: #878b96;
    --text: #333333;
    --twitter-blue: #5aa9d6;
    --facebook-blue: #3b5c97;
  }
  * { box-sizing: border-box; margin: 0; padding: 0; }
  html, body { width: 1200px; height: 374px; overflow: hidden; }
  body { background: var(--backdrop); position: relative; }

  .card {
    position: absolute; top: 33px; width: 525px; height: 298px;
    background: var(--card); border: 1px solid var(--card-edge);
    border-radius: 18px; overflow: hidden;
  }
  .card--front { left: 55px; }
  .card--back { left: 620px; }

  .brand-dot { position: absolute; border-radius: 50%; background: var(--ink); }
  .brand-name {
    position: absolute; font-family: "Marcellus", serif; color: var(--ink);
    white-space: nowrap; letter-spacing: 0.5px; text-align: center; line-height: 1;
  }
  .brand-rule { position: absolute; height: 1px; background: var(--ink); }
  .brand-tagline {
    position: absolute; font-family: "Marcellus", serif; color: var(--ink);
    letter-spacing: 2px; white-space: nowrap; text-align: center; line-height: 1;
  }

  /* front */
  .card--front .brand-dot { left: 90px; top: 24px; width: 76px; height: 76px; }
  .card--front .brand-name { left: 25px; top: 110px; width: 210px; font-size: 21px; }
  .card--front .brand-rule { left: 25px; top: 132px; width: 210px; }
  .card--front .brand-tagline { left: 25px; top: 137px; width: 210px; font-size: 8.5px; }

  .holder-name {
    position: absolute; left: 25px; top: 151px;
    font-family: "Tinos", serif; font-size: 13px; color: var(--ink); line-height: 1;
  }
  .contact-list {
    position: absolute; left: 25px; top: 170px; list-style: none;
    font-family: "Tinos", serif; font-size: 13px; color: var(--text); line-height: 18px;
  }
  .contact-list li { display: flex; align-items: center; gap: 5px; white-space: nowrap; }
  .contact-icon { width: 9px; height: 9px; flex: none; }
  .social-square { width: 9px; height: 9px; flex: none; border-radius: 1px; }
  .social-square--a { background: var(--twitter-blue); }
  .social-square--b { background: var(--facebook-blue); }
  .address {
    position: absolute; left: 25px; top: 268px; white-space: nowrap;
    font-family: "Tinos", serif; font-size: 14px; color: var(--text); line-height: 1.1;
  }
  .brand-feature {
    position: absolute; left: 264px; top: 29px; width: 254px; height: 234px;
    border-radius: 8px;
    background: linear-gradient(90deg, #8a8e98 0%, #9a9ea8 48%, #d8e6c4 60%, #fbe6b8 78%, #cfe0f1 100%);
    opacity: 0.85;
  }

  /* back */
  .card--back .brand-dot { left: 224px; top: 55px; width: 76px; height: 76px; }
  .card--back .brand-name { left: 112px; top: 165px; width: 300px; font-size: 26px; }
  .card--back .brand-rule { left: 130px; top: 193px; width: 264px; }
  .card--back .brand-tagline { left: 112px; top: 200px; width: 300px; font-size: 11px; }
  .back-web {
    position: absolute; left: 0; top: 244px; width: 525px; text-align: center;
    font-family: "Lato", sans-serif; font-size: 12.5px; letter-spacing: 2.4px; color: var(--text);
  }
</style>
</head>
<body>
  <section class="card card--front" aria-label="Card front">
    <div class="brand-dot"></div>
    <div class="brand-name">VISTALUME WORKS</div>
    <div class="brand-rule"></div>
    <div class="brand-tagline">FINE ART PHOTOGRAPHY</div>

    <div class="holder-name">Wiktor Baranowski</div>
    <ul class="contact-list">
      <li>
        <svg class="contact-icon" viewBox="0 0 10 10"><rect x="2.5" y="0.5" width="5" height="9" rx="1" fill="#555"/><rect x="3.5" y="1.8" width="3" height="5" fill="#fff"/></svg>
        0417 539 662
      </li>
      <li>
        <svg class="contact-icon" viewBox="0 0 10 10"><rect x="0.5" y="2" width="9" height="6" fill="#555"/><path d="M0.5 2 L5 5.5 L9.5 2" stroke="#fff" stroke-width="0.8" fill="none"/></svg>
        sales@vistalumeworks.com.au
      </li>
      <li>
        <svg class="contact-icon" viewBox="0 0 10 10"><circle cx="5" cy="5" r="4.5" fill="#555"/></svg>
        www.vistalumeworks.com.au
      </li>
      <li><span class="social-square social-square--a"></span>vistalumeworks</li>
      <li><span class="social-square social-square--b"></span>vistalumeworks</li>
    </ul>
    <div class="address">14 Harbour Lane, Fremantle WA 6160</div>

    <div class="brand-feature" role="img" aria-label="Large brand emblem decoration in grey with pastel leaf tones"></div>
  </section>

  <section class="card card--back" aria-label="Card back">
    <div class="brand-dot"></div>
    <div class="brand-name">VISTALUME WORKS</div>
    <div class="brand-rule"></div>
    <div class="brand-tagline">FINE ART PHOTOGRAPHY</div>
    <div class="back-web">www.vistalumeworks.com.au</div>
  </section>
</body>
</html>
```